Business card for law firm

Need business card for new law firm. Think confident, authoritative, conservative, but not stuffy or old-fashioned.

Contact Information for Business Card

Content for card - logo (uploaded), plus the following:

Paul Whitcombe (larger font)
Managing Partner (larger font, but not as large as name)
Level 9, 7 Ferris Lane
Sydney NSW 2000
Main Tel 02 9364 2710
Direct Tel 02 8472 3159
Email paul@qvlegal.com.au
www.qvlegal.com.au

Letterhead design should include logo plus:
Level 9, 7 Ferris Lane
Sydney NSW 2000
Tel 02 8472 3159
www.qvlegal.com.au

```html
<!DOCTYPE html>
<html lang="en">
<head>
<meta charset="utf-8">
<title>Quayvale Lawyers – Business Card</title>
<link rel="stylesheet" href="https://fonts.googleapis.com/css2?family=Ubuntu:wght@400;500&family=Roboto:wght@400&display=swap">
<style>
  :root {
    --navy: #070f6f;
    --ink: #111111;
    --white: #ffffff;
    --title-tint: #c9d3ea;
    --divider: #4b5aa6;
  }
  * { margin: 0; padding: 0; box-sizing: border-box; }
  html, body {
    width: 1200px;
    height: 686px;
    overflow: hidden;
    background: var(--white);
  }
  .card {
    position: relative;
    width: 1200px;
    height: 686px;
    background: var(--white);
    overflow: hidden;
  }
  .brand-mark {
    position: absolute;
    left: 548px;
    top: 60px;
    width: 104px;
    height: 104px;
    background: var(--navy);
  }
  .brand-name {
    position: absolute;
    left: 0;
    top: 292px;
    width: 1200px;
    text-align: center;
    font-family: "Ubuntu", "Helvetica Neue", sans-serif;
    font-weight: 400;
    font-size: 72px;
    line-height: 90px;
    color: var(--ink);
  }
  .contact-band {
    position: absolute;
    left: 0;
    top: 466px;
    width: 1200px;
    height: 220px;
  }
  .contact-band polygon { fill: var(--navy); }
  .person {
    position: absolute;
    right: 620px;
    top: 534px;
    text-align: right;
  }
  .person__name {
    font-family: "Ubuntu", "Helvetica Neue", sans-serif;
    font-weight: 500;
    font-size: 46px;
    line-height: 50px;
    color: var(--white);
    letter-spacing: 1px;
  }
  .person__title {
    font-family: "Ubuntu", "Helvetica Neue", sans-serif;
    font-weight: 400;
    font-size: 27px;
    line-height: 30px;
    color: var(--title-tint);
  }
  .divider {
    position: absolute;
    left: 632px;
    top: 483px;
    width: 2px;
    height: 186px;
    background: var(--divider);
  }
  .contact-list {
    position: absolute;
    left: 0;
    top: 0;
    list-style: none;
  }
  .contact-item {
    position: absolute;
    left: 680px;
    width: 440px;
    display: flex;
    align-items: flex-start;
    font-family: "Roboto", "Helvetica Neue", sans-serif;
    font-size: 19.5px;
    line-height: 23px;
    color: var(--white);
  }
  .contact-item svg {
    width: 24px;
    height: 24px;
    margin-right: 32px;
    flex: none;
    fill: var(--white);
  }
  .contact-item--address { top: 488px; }
  .contact-item--phone { top: 543px; }
  .contact-item--email { top: 595px; }
  .contact-item--web { top: 621px; }
</style>
</head>
<body>
<div class="card">
  <div class="brand-mark" aria-hidden="true"></div>
  <div class="brand-name">Quayvale Lawyers</div>

  <svg class="contact-band" viewBox="0 0 1200 220" aria-hidden="true">
    <polygon points="86,0 1102,0 1200,49 1200,220 0,220 0,49"/>
  </svg>

  <div class="person">
    <div class="person__name">Paul Whitcombe</div>
    <div class="person__title">Managing Partner</div>
  </div>

  <div class="divider" aria-hidden="true"></div>

  <ul class="contact-list">
    <li class="contact-item contact-item--address">
      <svg viewBox="0 0 24 24" aria-hidden="true"><path d="M12 2a7 7 0 0 0-7 7c0 5 7 13 7 13s7-8 7-13a7 7 0 0 0-7-7zm0 9.5a2.5 2.5 0 1 1 0-5 2.5 2.5 0 0 1 0 5z"/></svg>
      <span>Level 9, 7 Ferris Lane<br>Sydney NSW 2000</span>
    </li>
    <li class="contact-item contact-item--phone">
      <svg viewBox="0 0 24 24" aria-hidden="true"><path d="M7 2h10a2 2 0 0 1 2 2v16a2 2 0 0 1-2 2H7a2 2 0 0 1-2-2V4a2 2 0 0 1 2-2zm0 3v13h10V5H7zm5 14.2a1 1 0 1 0 0 2 1 1 0 0 0 0-2z"/></svg>
      <span>02 9364 2710<br>02 8472 3159</span>
    </li>
    <li class="contact-item contact-item--email">
      <svg viewBox="0 0 24 24" aria-hidden="true"><path d="M3 9l9-6 9 6v11H3V9zm2 1.6V18h14v-7.4l-7 4.6-7-4.6z"/></svg>
      <span>paul@qvlegal.com.au</span>
    </li>
    <li class="contact-item contact-item--web">
      <svg viewBox="0 0 24 24" aria-hidden="true"><path d="M12 2a10 10 0 1 0 0 20 10 10 0 0 0 0-20zm6.9 9h-3a15 15 0 0 0-1.2-6.1A8 8 0 0 1 18.9 11zM12 4.1c.9 1.2 1.8 3.6 1.9 6.9h-3.8c.1-3.3 1-5.7 1.9-6.9zM9.3 4.9A15 15 0 0 0 8.1 11h-3a8 8 0 0 1 4.2-6.1zM5.1 13h3a15 15 0 0 0 1.2 6.1A8 8 0 0 1 5.1 13zm6.9 6.9c-.9-1.2-1.8-3.6-1.9-6.9h3.8c-.1 3.3-1 5.7-1.9 6.9zm2.7-.8a15 15 0 0 0 1.2-6.1h3a8 8 0 0 1-4.2 6.1z"/></svg>
      <span>www.qvlegal.com.au</span>
    </li>
  </ul>
</div>
</body>
</html>
```